Pinecrest Harbor Foundation Web Design

The design we need is for a WordPress blog that will be our content platform. We are a registered 501(c)3 non-profit that focuses on financially supporting the treatment of cancer patients that have been told they have no hope and there is nothing the conventional medical system can do for them. Through this wesbite we want to both rasie awareness about the treatment options plus, raise funds for treating patients. The two primary target audiences of the site are...

1. Terminally ill patients and their families to let them know that there is an option other then hospice and that we are hear to support that option.

2. People looking to help donate to a worthwhile cause that resonates with them.

The website is https://pinecrestharborfoundation.org/

See attached logo designs!!!

Target Market(s)

Cancer patients and their families

Industry/Entity Type

Foundation

Font styles to use
Sans Serif

Colors
ffffff
fbed22

Requirements
Must have
• I like this look of this site. It is clean, simple, helpful, soft. I like the flow of the pages.
• http://www.meadowsforcalm.org/
• I like the design and flow but NOT the color or boldness
• https://tvbn-youth.org/
• I like this style for a donation page.
• https://www.tumorstudyhub.org/we-are-tsh/join-the-cause/donations/one-time-donation
• with the addition of a Would you like your employer to match? button.
Nice to have
• White black and gold - but soft
• Even possibly grayscale like the site I like.

```html
<!DOCTYPE html>
<html lang="en">
<head>
<meta charset="utf-8">
<title>Pinecrest Harbor Foundation</title>
<link href="https://fonts.googleapis.com/css2?family=Cinzel:wght@400;700&family=Montserrat:wght@400;500;600&display=swap" rel="stylesheet">
<style>
:root{
  --gold:#ecc95a;
  --gold-deep:#e2b83e;
  --ink:#111111;
  --dark:#1a1a1a;
  --white:#ffffff;
  --muted:#9a9a9a;
  --text:#333333;
  --footer-text:#bdbdbd;
  --social-1:#4a5f8f;
  --social-2:#4fb3e8;
  --social-3:#d7574a;
  --social-4:#2f7fb5;
}
*{margin:0;padding:0;box-sizing:border-box}
html,body{width:1200px;height:3475px;overflow:hidden}
body{font-family:"Montserrat",Arial,sans-serif;color:var(--text);background:var(--white);position:relative}
.serif{font-family:"Cinzel",Georgia,serif}
.hex{display:inline-flex;align-items:center;justify-content:center;background:var(--gold);color:var(--white);font-family:"Cinzel",Georgia,serif;letter-spacing:1px;clip-path:polygon(10% 0,90% 0,100% 50%,90% 100%,10% 100%,0 50%)}
.photo{position:absolute;inset:0}

/* Hero */
.hero{position:absolute;top:0;left:0;width:1200px;height:679px;overflow:hidden}
.hero-photo{background:
  radial-gradient(ellipse 360px 420px at 640px 300px,rgba(235,235,235,.85),rgba(235,235,235,0) 70%),
  radial-gradient(ellipse 300px 380px at 1050px 320px,rgba(120,120,120,.6),rgba(120,120,120,0) 70%),
  radial-gradient(ellipse 260px 300px at 120px 330px,rgba(200,200,200,.55),rgba(200,200,200,0) 70%),
  linear-gradient(180deg,#7a7a7a 0%,#9e9e9e 45%,#5c5c5c 100%)}
.hero-shade{background:linear-gradient(90deg,rgba(0,0,0,.45) 0%,rgba(0,0,0,.15) 55%,rgba(0,0,0,0) 100%),linear-gradient(0deg,rgba(0,0,0,.35) 0%,rgba(0,0,0,0) 45%)}
.topbar{position:absolute;top:0;left:0;width:1200px;height:115px;background:rgba(0,0,0,.35)}
.brand{position:absolute;left:76px;top:34px;display:flex;align-items:center;gap:12px;color:var(--white);font-family:"Cinzel",Georgia,serif;font-size:20px;font-weight:700;line-height:1.15;width:300px}
.brand-dot{width:40px;height:40px;border-radius:50%;background:var(--gold);flex:none}
.nav{position:absolute;right:81px;top:40px;display:flex;align-items:center;gap:28px;font-size:14px;color:var(--white);text-transform:uppercase}
.nav .active{border-bottom:2px solid var(--white)}
.nav .hex{width:152px;height:52px;font-size:20px}
.hero-title{position:absolute;left:76px;top:420px;color:var(--white);font-size:42px;font-weight:600;letter-spacing:1px}
.hero-sub{position:absolute;left:79px;top:484px;width:720px;color:var(--white);font-size:16px;line-height:26px}
.hero-btns{position:absolute;left:81px;top:549px;display:flex;gap:13px}
.hero-btns .hex{width:179px;height:53px;font-size:24px}

/* About */
.about{position:absolute;top:679px;left:0;width:1200px;height:505px}
.about-title{position:absolute;left:79px;top:96px;font-size:42px;color:var(--ink);font-weight:400;letter-spacing:1px}
.about-sub{position:absolute;left:81px;top:154px;font-size:20px;color:var(--ink);display:flex;align-items:center;gap:14px;width:420px}
.about-sub span.rule{flex:1;height:1px;background:#cccccc}
.about-copy{position:absolute;left:79px;top:202px;width:690px;font-size:12.5px;line-height:29px;color:var(--muted)}
.about-copy p+p{margin-top:4px}
.about .hex{position:absolute;left:81px;top:354px;width:204px;height:58px;font-size:24px}
.ribbon{position:absolute;left:800px;top:58px;width:300px;height:410px;background:radial-gradient(ellipse 140px 200px at 50% 48%,#f5cf3c 0%,#efc43a 45%,rgba(255,255,255,0) 100%)}

/* Support band */
.band{position:absolute;top:1184px;left:0;width:1200px;height:415px;background:radial-gradient(ellipse 260px 300px at 720px 220px,rgba(200,150,60,.35),rgba(200,150,60,0) 70%),linear-gradient(90deg,var(--gold),var(--gold-deep));text-align:center;color:var(--white)}
.band h2{position:absolute;top:64px;width:100%;font-size:46px;color:var(--ink);font-weight:400}
.band p{position:absolute;top:134px;left:200px;width:800px;font-size:16px;line-height:28px}
.band-call{position:absolute;top:205px;width:100%;display:flex;justify-content:center;align-items:center;gap:22px;font-size:28px}
.band-call .label{font-family:"Cinzel",Georgia,serif;font-weight:700;letter-spacing:1px}
.phone-circle{width:64px;height:64px;border-radius:50%;background:var(--white);display:flex;align-items:center;justify-content:center}
.band-mail{position:absolute;top:300px;width:100%;font-size:22px;text-decoration:underline;font-style:italic}

/* Audience cards */
.audience{position:absolute;top:1599px;left:0;width:1200px;height:572px}
.card{position:absolute;top:81px;width:501px}
.card-photo{height:331px;position:relative;overflow:hidden}
.card-tag{position:absolute;left:0;bottom:0;width:100%;height:90px;background:var(--gold);clip-path:polygon(0 100%,0 70%,50% 0,100% 70%,100% 100%);text-align:center;color:var(--white);font-family:"Cinzel",Georgia,serif}
.card-tag .num{display:block;padding-top:18px;font-size:34px;line-height:34px}
.card-tag .name{display:block;font-size:21px;letter-spacing:1px;margin-top:6px}
.card p{margin-top:26px;font-size:15px;line-height:28px;color:var(--text);width:470px}
.photo-family{background:
  radial-gradient(ellipse 110px 130px at 170px 150px,rgba(240,210,190,.7),rgba(240,210,190,0) 70%),
  radial-gradient(ellipse 110px 130px at 320px 140px,rgba(230,200,180,.7),rgba(230,200,180,0) 70%),
  radial-gradient(ellipse 140px 80px at 250px 260px,rgba(190,40,60,.55),rgba(190,40,60,0) 70%),
  linear-gradient(180deg,#8f8068 0%,#b8a88e 50%,#6d6253 100%)}
.photo-group{background:
  radial-gradient(ellipse 260px 90px at 250px 270px,rgba(236,120,160,.85),rgba(236,120,160,0) 75%),
  radial-gradient(ellipse 220px 110px at 250px 140px,rgba(225,190,170,.7),rgba(225,190,170,0) 70%),
  linear-gradient(180deg,#3e3535 0%,#8a6a6a 45%,#d77fa3 100%)}

/* Hospitality */
.hospitality{position:absolute;top:2171px;left:0;width:1200px;height:394px;background:
  radial-gradient(ellipse 300px 200px at 150px 330px,rgba(120,70,50,.45),rgba(120,70,50,0) 70%),
  radial-gradient(ellipse 300px 200px at 1050px 330px,rgba(120,70,50,.45),rgba(120,70,50,0) 70%),
  linear-gradient(180deg,#1f1f1f,#3a302c 60%,#2a2525)}
.hospitality h2{position:absolute;top:56px;width:100%;text-align:center;font-size:43px;color:var(--white);font-weight:400}
.help-box{position:absolute;top:2308px;left:287px;width:624px;height:292px;background:var(--white);border-radius:6px;box-shadow:0 4px 14px rgba(0,0,0,.25);text-align:center;z-index:2}
.help-box p{margin:26px auto 0;width:540px;font-size:15px;line-height:26px;color:#555}
.help-box .hex{width:460px;height:56px;font-size:22px;margin-top:16px}
.help-box .hex:first-of-type{margin-top:24px}

/* News */
.news{position:absolute;top:2565px;left:0;width:1200px;height:466px}
.news h2{position:absolute;top:84px;width:100%;text-align:center;font-size:44px;color:var(--ink);font-weight:700;letter-spacing:1px}
.post{position:absolute;top:185px;width:325px;height:218px;overflow:hidden}
.post-label{position:absolute;left:0;top:116px;width:230px;height:54px;display:flex;align-items:center;padding-left:24px;font-family:"Cinzel",Georgia,serif;font-size:22px;color:var(--white);clip-path:polygon(0 0,88% 0,100% 50%,88% 100%,0 100%)}
.post-label.gold{background:var(--gold)}
.post-label.black{background:var(--ink)}
.photo-balloons{background:
  radial-gradient(circle 50px at 60px 50px,rgba(60,110,200,.9),rgba(60,110,200,0) 70%),
  radial-gradient(circle 55px at 250px 60px,rgba(230,210,60,.9),rgba(230,210,60,0) 70%),
  radial-gradient(circle 60px at 170px 180px,rgba(150,200,90,.8),rgba(150,200,90,0) 70%),
  linear-gradient(180deg,#8fb0d8,#d9d4b0)}
.photo-study{background:
  radial-gradient(ellipse 140px 70px at 160px 70px,rgba(110,95,80,.55),rgba(110,95,80,0) 70%),
  linear-gradient(180deg,#c9c2b8 0%,#ece9e4 60%,#f6f4f0 100%)}
.photo-sign{background:
  radial-gradient(ellipse 90px 80px at 220px 60px,rgba(210,40,80,.9),rgba(210,40,80,0) 70%),
  radial-gradient(ellipse 120px 90px at 230px 170px,rgba(220,220,225,.6),rgba(220,220,225,0) 70%),
  linear-gradient(135deg,#3a2a30,#7a2a40 55%,#4a4a4a)}

/* Footer */
.footer-nav{position:absolute;top:3031px;left:0;width:1200px;height:76px;background:var(--gold);display:flex;align-items:center;padding:0 76px;justify-content:space-between}
.footer-nav ul{list-style:none;display:flex;gap:26px;font-size:14px;color:var(--white);text-transform:uppercase}
.socials{display:flex;gap:12px}
.socials span{width:44px;height:44px;border-radius:50%;border:3px solid var(--white)}
.socials .s1{background:var(--social-1)}
.socials .s2{background:var(--social-2)}
.socials .s3{background:var(--social-3)}
.socials .s4{background:var(--social-4)}
.footer{position:absolute;top:3107px;left:0;width:1200px;height:368px;background:var(--dark);color:var(--footer-text)}
.footer h3{font-family:"Cinzel",Georgia,serif;font-weight:400;font-size:17px;color:var(--gold);letter-spacing:1px}
.f-brand{position:absolute;left:76px;top:48px;width:330px}
.f-brand .brand-name{font-family:"Cinzel",Georgia,serif;font-weight:700;font-size:22px;color:var(--white);line-height:1.15;display:flex;align-items:center;gap:12px}
.f-brand p{margin-top:30px;font-size:13px;line-height:24px}
.f-tweets{position:absolute;left:436px;top:42px;width:330px}
.tweet{display:flex;gap:16px;margin-top:26px;font-size:12.5px;line-height:23px}
.tweet .dot{width:30px;height:30px;border-radius:50%;background:#4fb3e8;flex:none}
.tweet b{color:#4fb3e8;font-weight:500}
.f-contact{position:absolute;left:790px;top:42px;width:340px}
.f-row{display:flex;gap:20px;margin-top:22px;font-size:13px;line-height:23px}
.f-row .icon{width:24px;flex:none;display:flex;justify-content:center;padding-top:2px}
.f-row strong{color:var(--gold);font-family:"Cinzel",Georgia,serif;font-weight:400;font-size:14px;display:block}
.copyright{position:absolute;left:0;top:326px;width:100%;text-align:center;font-size:13px}
.copyright .name{color:var(--gold)}
</style>
</head>
<body>

<header class="hero">
  <div class="photo hero-photo" role="img" aria-label="Black and white photo of a smiling young child in a tough-guy t-shirt holding an adult's hand"></div>
  <div class="photo hero-shade"></div>
  <div class="topbar"></div>
  <div class="brand"><span class="brand-dot"></span>Pinecrest Harbor Foundation</div>
  <nav class="nav">
    <span class="active">Home</span><span>About</span><span>Donate</span><span>Support Hospitality</span><span>News</span>
    <span class="hex">Contact</span>
  </nav>
  <h1 class="hero-title">HELP FOR FIGHT CANCER</h1>
  <p class="hero-sub">Financially Supporting The Treatment Of Cancer Patients that have been told they have no hope and there is nothing the conventional medical system can do for them.</p>
  <div class="hero-btns"><span class="hex">Donate</span><span class="hex">Support</span></div>
</header>

<section class="about">
  <h2 class="about-title serif">Pinecrest Harbor</h2>
  <div class="about-sub serif">Foundation <span class="rule"></span></div>
  <div class="about-copy">
    <p>Lorem Ipsum is simply dummy text of the printing and typesetting industry. Lorem Ipsum has been the industry's standard dummy text ever since the 1500s, when an unknown.</p>
    <p>Lorem Ipsum is simply dummy text of the printing and typesetting industry. Lorem Ipsum has been the industry's standard dummy text ever since the 1500s, when an unknown printer took a galley of type and scrambled it to make a type specimen book. It has survived not only five centuries, but also the leap into.</p>
  </div>
  <span class="hex">Learn More</span>
  <div class="ribbon" role="img" aria-label="Gold awareness ribbon"></div>
</section>

<section class="band">
  <h2 class="serif">Get Our Support For......</h2>
  <p>Financially Supporting The Treatment Of Cancer Patients that have been told they have no hope and there is nothing the conventional medical system can do for them.</p>
  <div class="band-call">
    <span class="label">Call Us Today :</span>
    <span class="phone-circle">
      <svg width="30" height="30" viewBox="0 0 24 24"><path fill="#e2b83e" d="M6.6 10.8a15.1 15.1 0 0 0 6.6 6.6l2.2-2.2a1 1 0 0 1 1-.25 11.4 11.4 0 0 0 3.6.57 1 1 0 0 1 1 1V20a1 1 0 0 1-1 1A17 17 0 0 1 3 4a1 1 0 0 1 1-1h3.5a1 1 0 0 1 1 1c0 1.25.2 2.45.57 3.57a1 1 0 0 1-.25 1z"/></svg>
    </span>
    <span>123 456 7890</span>
  </div>
  <div class="band-mail">info@PinecrestHarbor.com</div>
</section>

<section class="audience">
  <article class="card" style="left:76px">
    <div class="card-photo">
      <div class="photo photo-family" role="img" aria-label="Photo of a family of two adults and two small children on a sofa"></div>
      <div class="card-tag"><span class="num">1</span><span class="name">Pinecrest Harbor</span></div>
    </div>
    <p>Terminally Ill Patients And Their Families To Let Them Know That There Is An Option Other Then Hospice And That We Are Hear To Support That Option.</p>
  </article>
  <article class="card" style="left:623px">
    <div class="card-photo">
      <div class="photo photo-group" role="img" aria-label="Photo of a group of smiling women in pink shirts"></div>
      <div class="card-tag"><span class="num">2</span><span class="name">Pinecrest Harbor</span></div>
    </div>
    <p>People Looking To Help Donate To A Worthwhile Cause That Resonates With Them</p>
  </article>
</section>

<section class="hospitality" role="img" aria-label="Dark photo of raised hands in a crowd">
  <h2 class="serif">Support Hospitality</h2>
</section>
<div class="help-box">
  <p>Cancer support is an integral part to treating the whole patient. Learn why support is so important to an integrated approach to your care.</p>
  <span class="hex">Why Do I Need Support ?</span><br>
  <span class="hex">Should I Join a Support Group</span>
</div>

<section class="news">
  <h2 class="serif">Latest News</h2>
  <article class="post" style="left:76px">
    <div class="photo photo-balloons" role="img" aria-label="Photo of people with colourful balloons"></div>
    <div class="post-label gold">Lorem Ipsum</div>
  </article>
  <article class="post" style="left:438px">
    <div class="photo photo-study" role="img" aria-label="Photo of a group studying around a table"></div>
    <div class="post-label black">Lorem Ipsum</div>
  </article>
  <article class="post" style="left:799px">
    <div class="photo photo-sign" role="img" aria-label="Photo of hands holding an awareness sign"></div>
    <div class="post-label black">Lorem Ipsum</div>
  </article>
</section>

<nav class="footer-nav">
  <ul><li>Home</li><li>About</li><li>Donate</li><li>Support Hospitality</li><li>News</li></ul>
  <div class="socials"><span class="s1"></span><span class="s2"></span><span class="s3"></span><span class="s4"></span></div>
</nav>

<footer class="footer">
  <div class="f-brand">
    <div class="brand-name"><span class="brand-dot"></span>Pinecrest Harbor Foundation</div>
    <p>Lorem Ipsum is simply dummy text of the printing and typesetting industry. Lorem Ipsum has been the industry's standard dummy text ever since the 1500s, when an unknown.....</p>
  </div>
  <div class="f-tweets">
    <h3>Latest Twits</h3>
    <div class="tweet"><span class="dot"></span><span><b>#Pinecrest Harbor Foundation @</b> Lorem Ipsum is simply dummy text of the printing and typesetting industry.</span></div>
    <div class="tweet"><span class="dot"></span><span><b>#Pinecrest Harbor Foundation @</b> Lorem Ipsum is simply dummy text of the printing and typesetting industry.</span></div>
  </div>
  <div class="f-contact">
    <h3>Contact Us</h3>
    <div class="f-row">
      <span class="icon"><svg width="20" height="28" viewBox="0 0 20 28"><path fill="#ecc95a" d="M10 0a10 10 0 0 0-10 10c0 7 10 18 10 18s10-11 10-18A10 10 0 0 0 10 0zm0 14a4 4 0 1 1 0-8 4 4 0 0 1 0 8z"/></svg></span>
      <span><strong>Pinecrest Harbor Foundation</strong>Lorem Ipsum is simply dummy text of the printing and typesetting industry. Lorem Ipsum has been the industry...</span>
    </div>
    <div class="f-row">
      <span class="icon"><svg width="18" height="18" viewBox="0 0 24 24"><path fill="#ecc95a" d="M6.6 10.8a15.1 15.1 0 0 0 6.6 6.6l2.2-2.2a1 1 0 0 1 1-.25 11.4 11.4 0 0 0 3.6.57 1 1 0 0 1 1 1V20a1 1 0 0 1-1 1A17 17 0 0 1 3 4a1 1 0 0 1 1-1h3.5a1 1 0 0 1 1 1c0 1.25.2 2.45.57 3.57a1 1 0 0 1-.25 1z"/></svg></span>
      <span>123 456 7890</span>
    </div>
    <div class="f-row">
      <span class="icon"><svg width="20" height="16" viewBox="0 0 20 16"><rect width="20" height="16" rx="2" fill="#ecc95a"/><path d="M1 2l9 7 9-7" stroke="#1a1a1a" stroke-width="1.6" fill="none"/></svg></span>
      <span>info@PinecrestHarbor.com</span>
    </div>
  </div>
  <div class="copyright"><span class="name">©Pinecrest Harbor Foundation</span> - 2017 All rights reserved | Terms of use | Privacy</div>
</footer>

</body>
</html>
```